Website Design for WestaKolory.pl – Luxury Wedding Car Rental with Chauffeur

We are looking for a talented designer to create a modern, elegant, and fully responsive website for our new brand – WestyKolory.pl. We are a premium car rental platform in Poland, offering luxury and exotic vehicles exclusively for weddings. All cars come with a professional chauffeur, ensuring a high-end, stress-free, and stylish experience.
Website Purpose:
The website should present our offering in a luxurious, clear, and inspiring way. It must build trust, highlight the prestige of our brand, and encourage inquiries. Our target audience includes engaged couples, wedding planners, and clients seeking a truly exceptional vehicle for their special day.
Design Requirements:
Style: modern, elegant, minimalist
Color palette: white, black, gold, optionally silver – refined and luxurious
Typography: clean, modern, high-end
Layout: clear, intuitive, with large car images and well-defined sections
Fully responsive (desktop, tablet, mobile)
Bilingual layout (Polish/English) must be considered
Pages to Design:
Homepage
About Us
Fleet Overview
Individual Car Pages
Services (Weddings, Photo Shoots, Film Rentals)
Why Us / Unique Selling Points
Contact
FAQ
Inspiration:
Luxury automotive brands (e.g. Varnel-Hoske, Corvash, Elbrin Tusko)
High-end wedding websites
Minimalist layouts with large visuals and elegant typography
Additional Notes:
The design should evoke the emotions of a wedding day – elegance, uniqueness, style, and class. Please avoid flashy colors, excessive graphic effects, or overly decorative elements. Subtlety, prestige, and sophistication are key.

```html
<!DOCTYPE html>
<html lang="en">
<head>
<meta charset="utf-8">
<title>WestaKolory.pl – Luxury Wedding Car Rental</title>
<link rel="stylesheet" href="https://fonts.googleapis.com/css2?family=Cormorant+Garamond:ital,wght@0,500;0,600;1,500&family=Lato:wght@300;400;700&display=swap">
<style>
:root{
  --navy:#16233a;
  --gold:#dbbf66;
  --white:#ffffff;
  --ink:#16233a;
  --muted:#c9ced8;
  --serif:'Cormorant Garamond', Georgia, serif;
  --sans:'Lato', Arial, sans-serif;
}
*{margin:0;padding:0;box-sizing:border-box}
html,body{width:1200px;height:3727px;overflow:hidden;background:var(--navy)}
body{font-family:var(--sans);color:var(--white)}
.page{position:relative;width:1200px;height:3727px;background:var(--navy)}
.abs{position:absolute}
.serif{font-family:var(--serif);font-weight:600}
.pill{position:absolute;border:1.5px solid var(--white);border-radius:40px;display:flex;align-items:center;justify-content:center;font-family:var(--sans);font-weight:700;color:var(--white)}
.pill.dark{border-color:var(--ink);color:var(--ink)}
.dot{position:absolute;border-radius:50%;background:var(--gold);display:flex;align-items:center;justify-content:center}
.dot.black{background:#111}

/* nav */
.brand{left:32px;top:18px;font-family:var(--serif);font-weight:600;font-size:26px;color:var(--gold);display:flex;align-items:center;gap:8px}
.brand .mark{width:14px;height:14px;border-radius:50%;background:var(--gold)}
.nav a{position:absolute;top:28px;font-size:19px;font-weight:700;color:var(--white);text-decoration:none;transform:translateX(-50%)}
.nav .lang-off{color:#bfc4cc}

/* hero */
.hero-photo{left:588px;top:0;width:612px;height:854px;background:linear-gradient(160deg,#cfc6bd 0%,#a99d92 35%,#e9e6e2 60%,#8d7f74 100%)}
.hero-title{left:33px;top:236px;font-size:76px;line-height:80px;color:var(--white)}
.hero-sub{left:33px;top:440px;font-size:19px;font-weight:400}

/* gold band */
.band{left:0;width:1200px;background:var(--gold);color:var(--ink)}
.band h2{position:absolute;width:100%;text-align:center;font-family:var(--serif);font-weight:600}
.tick{position:absolute;font-family:var(--serif);font-weight:500;font-size:26px;color:var(--ink)}

/* fleet banner */
.fleet-title{left:43px;top:1226px;font-size:29px}
.fleet-sub{left:43px;top:1259px;font-size:22px;font-weight:300;line-height:23px}
.fleet-cta{left:749px;top:1242px;font-size:40px;font-weight:700}

/* services */
.services-box{left:0;top:1392px;width:1200px;height:294px;border-top:1.5px solid var(--white);border-bottom:1.5px solid var(--white)}
.services-title{left:47px;top:1465px;font-size:46px}
.services-list{left:92px;top:1533px;font-size:23px;font-weight:300;line-height:33px;list-style:disc}
.frame{position:absolute;border:1.5px solid var(--white)}
.car-img{left:466px;top:1482px;width:274px;height:120px;border-radius:60px 80px 30px 30px;background:linear-gradient(180deg,#2a2a2a,#050505)}
.couple-img{left:832px;top:1448px;width:46px;height:188px;border-radius:20px 20px 6px 6px;background:linear-gradient(180deg,#cfc8c0,#3a3a3a 45%,#f2f0ee 55%,#e2dfdb)}

/* testimonials */
.quote{position:absolute;width:300px;text-align:center;font-size:15px;font-style:italic;font-weight:300;line-height:24px}
.quote .who{display:block;font-family:var(--serif);font-size:14px;margin-top:12px}
.testi-title{left:743px;top:1795px;width:457px;text-align:center;font-size:46px}

/* faq */
.faq-box{left:263px;top:2274px;width:674px;height:638px;border:1.5px solid var(--white);background:var(--navy)}
.faq-title{left:263px;top:2312px;width:674px;text-align:center;font-size:44px}
.faq-q{height:46px;width:448px;left:350px;font-size:19px}
.faq-a{left:350px;top:2470px;width:500px;font-size:19px;font-weight:300;line-height:20px}
.flowers{left:0;top:2663px;width:1200px;height:249px;background:linear-gradient(180deg,rgba(255,255,255,0) 0%,rgba(255,255,255,.55) 70%,rgba(255,255,255,.85) 100%)}

/* footer */
.footer{left:0;top:2912px;width:1200px;height:294px;border:1.5px solid var(--white)}
.footer-divider{left:738px;top:2912px;width:1.5px;height:294px;background:var(--white)}
.footer-title{left:57px;top:2950px;font-size:42px}
.copy{left:65px;top:3140px;font-size:22px;font-weight:300}
.fcol{position:absolute;top:2952px}
.fcol h4{font-family:var(--serif);font-weight:600;font-size:20px;margin-bottom:10px}
.fcol li{list-style:none;font-size:13px;line-height:25px}
.fcol.social li{line-height:33px}
.big-name{left:0;top:3300px;width:1200px;text-align:center;font-family:var(--serif);font-weight:600;font-size:210px;line-height:1;color:var(--gold)}
</style>
</head>
<body>
<div class="page">

  <!-- navigation -->
  <div class="abs brand"><span>WestaKolory</span><span class="mark"></span></div>
  <nav class="nav">
    <a style="left:269px">Home</a>
    <a style="left:401px">Fleet</a>
    <a style="left:541px">Services</a>
    <a style="left:695px">Why Us</a>
    <a style="left:840px">About</a>
    <a style="left:984px">Contact</a>
    <a style="left:1115px">PL</a>
    <a class="lang-off" style="left:1154px">EN</a>
  </nav>

  <!-- hero -->
  <div class="abs hero-photo" role="img" aria-label="Bride and groom embracing beside a vintage wedding car"></div>
  <h1 class="abs serif hero-title">Arrive in Style on<br>Your Special Day</h1>
  <p class="abs hero-sub">Luxury Wedding Car Rentals with Chauffeur Service</p>
  <div class="pill" style="left:33px;top:512px;width:196px;height:47px;font-size:19px">Explore Our Fleet</div>
  <div class="dot" style="left:240px;top:515px;width:42px;height:42px"><svg width="22" height="22" viewBox="0 0 22 22"><path d="M4 18L18 4M9 4h9v9" stroke="#fff" stroke-width="1.6" fill="none"/></svg></div>
  <div class="pill" style="left:81px;top:573px;width:148px;height:45px;font-size:19px">Get a Quote</div>
  <div class="dot" style="left:240px;top:575px;width:42px;height:42px"><svg width="22" height="22" viewBox="0 0 22 22"><path d="M4 18L18 4M9 4h9v9" stroke="#fff" stroke-width="1.6" fill="none"/></svg></div>

  <!-- premium band -->
  <section class="abs band" style="top:854px;height:287px">
    <h2 style="top:46px;font-size:42px">A Premium Experience for Life’s Most Elegant Moments</h2>
    <span class="tick" style="left:156px;top:127px">✓ Exclusive luxury &amp; exotic vehicles</span>
    <span class="tick" style="left:559px;top:127px">✓ Tailored for weddings and styled shoots</span>
    <span class="tick" style="left:156px;top:182px">✓ Professional, punctual chauffeurs</span>
    <span class="tick" style="left:559px;top:182px">✓ Trusted by wedding planners across Poland</span>
  </section>

  <!-- fleet banner -->
  <svg class="abs" style="left:0;top:1195px" width="1200" height="145" viewBox="0 0 1200 145">
    <path d="M0 6H591L517 137H0" stroke="#fff" stroke-width="1.5" fill="none"/>
    <path d="M1200 6H630L550 137H1200" stroke="#fff" stroke-width="1.5" fill="none"/>
  </svg>
  <div class="abs serif fleet-title">A Curated Fleet for Unforgettable Entrances</div>
  <div class="abs fleet-sub">From vintage elegance to modern<br>opulence — our cars are ready to impress.</div>
  <div class="abs fleet-cta">View Full Fleet</div>
  <div class="dot" style="left:1037px;top:1231px;width:68px;height:68px"><svg width="34" height="34" viewBox="0 0 22 22"><path d="M4 18L18 4M9 4h9v9" stroke="#fff" stroke-width="1.4" fill="none"/></svg></div>

  <!-- services -->
  <div class="abs services-box"></div>
  <h2 class="abs serif services-title">More Than Just a Ride</h2>
  <ul class="abs services-list">
    <li>Wedding Day Rental</li>
    <li>Engagement Photoshoots</li>
    <li>Film &amp; Editorial Rentals</li>
  </ul>
  <div class="frame" style="left:453px;top:1432px;width:300px;height:214px"></div>
  <div class="abs car-img" role="img" aria-label="Black sports coupe"></div>
  <div class="frame" style="left:776px;top:1432px;width:158px;height:214px"></div>
  <div class="abs couple-img" role="img" aria-label="Wedding couple standing together"></div>
  <div class="pill" style="left:955px;top:1518px;width:174px;height:43px;font-size:17px">Discover Services</div>
  <div class="dot" style="left:1139px;top:1521px;width:36px;height:36px"><svg width="18" height="18" viewBox="0 0 22 22"><path d="M4 18L18 4M9 4h9v9" stroke="#fff" stroke-width="1.8" fill="none"/></svg></div>

  <!-- testimonials -->
  <svg class="abs" style="left:0;top:1740px" width="1200" height="173" viewBox="0 0 1200 173">
    <path d="M0 1H646A85 85 0 0 1 646 171H0" stroke="#fff" stroke-width="1.5" fill="none"/>
    <path d="M1200 1H828A85 85 0 0 0 828 171H1200" stroke="#fff" stroke-width="1.5" fill="none"/>
    <path d="M40 158H68M72 158H98M102 158H133" stroke="#fff" stroke-width="2"/>
  </svg>
  <p class="quote" style="left:47px;top:1783px">“Our wedding felt like a fairytale. The car and chauffeur were perfect!”<span class="who">Ewa &amp; Marek</span></p>
  <p class="quote" style="left:393px;top:1783px">“Our wedding felt like a fairytale. The car and chauffeur were perfect!”<span class="who">Ewa &amp; Marek</span></p>
  <h2 class="abs serif testi-title">What Our Couples Say</h2>

  <!-- CTA band -->
  <section class="abs band" style="top:1966px;height:257px">
    <h2 style="top:50px;font-size:46px">Let’s Make Your Wedding Unforgettable</h2>
    <p class="abs serif" style="top:111px;width:100%;text-align:center;font-size:26px;font-weight:500">Send us a message or request a custom quote.</p>
  </section>
  <div class="pill dark" style="left:499px;top:2125px;width:148px;height:45px;font-size:19px">Get a Quote</div>
  <div class="dot black" style="left:659px;top:2126px;width:42px;height:42px"><svg width="22" height="22" viewBox="0 0 22 22"><path d="M4 18L18 4M9 4h9v9" stroke="#fff" stroke-width="1.6" fill="none"/></svg></div>

  <!-- faq -->
  <div class="abs flowers" role="img" aria-label="White floral silhouettes along the bottom edge"></div>
  <div class="abs faq-box"></div>
  <h2 class="abs serif faq-title">Your doubts, answered with elegance.</h2>
  <div class="pill faq-q" style="top:2400px">What types of cars do you offer for weddings?</div>
  <div class="dot" style="left:808px;top:2402px;width:42px;height:42px"><svg width="20" height="20" viewBox="0 0 20 20"><path d="M4 10H16" stroke="#fff" stroke-width="2"/></svg></div>
  <p class="abs faq-a">We offer a curated selection of luxury and exotic cars — including Varnel-Hoske, Corvash, Meridan-Kraft, and more — all equipped with a professional chauffeur for a seamless experience.</p>
  <div class="pill faq-q" style="top:2575px">Can we view the cars before booking?</div>
  <div class="dot" style="left:808px;top:2577px;width:42px;height:42px"><svg width="20" height="20" viewBox="0 0 20 20"><path d="M4 10H16M10 4V16" stroke="#fff" stroke-width="2"/></svg></div>
  <div class="pill faq-q" style="top:2646px">Do the rentals include a chauffeur?</div>
  <div class="dot" style="left:808px;top:2648px;width:42px;height:42px"><svg width="20" height="20" viewBox="0 0 20 20"><path d="M4 10H16M10 4V16" stroke="#fff" stroke-width="2"/></svg></div>
  <div class="pill faq-q" style="top:2717px">Can we decorate the car ourselves?</div>
  <div class="dot" style="left:808px;top:2719px;width:42px;height:42px"><svg width="20" height="20" viewBox="0 0 20 20"><path d="M4 10H16M10 4V16" stroke="#fff" stroke-width="2"/></svg></div>
  <div class="pill faq-q" style="top:2788px">How far in advance should we book?</div>
  <div class="dot" style="left:808px;top:2790px;width:42px;height:42px"><svg width="20" height="20" viewBox="0 0 20 20"><path d="M4 10H16M10 4V16" stroke="#fff" stroke-width="2"/></svg></div>

  <!-- footer -->
  <footer>
    <div class="abs footer"></div>
    <div class="abs footer-divider"></div>
    <h2 class="abs serif footer-title">Arrive in Style on Your Special Day</h2>
    <p class="abs copy">© 2025 WestaKolory.pl | Luxury Wedding Car Rental Poland</p>
    <div class="fcol" style="left:782px"><h4>Navigation</h4><ul><li>Home</li><li>Fleet</li><li>Services</li><li>Why Us</li><li>About</li><li>Contact</li></ul></div>
    <div class="fcol" style="left:939px"><h4>Language</h4><ul><li>PL&nbsp;&nbsp;&nbsp;<span style="color:var(--muted)">EN</span></li></ul></div>
    <div class="fcol social" style="left:1086px"><h4>Social</h4><ul style="margin-top:-4px"><li>Facelane</li><li>Instaframe</li><li>Linkpro</li><li>Vidtube</li><li>Zed</li></ul></div>
    <div class="abs big-name">WestaKolory</div>
  </footer>

</div>
</body>
</html>
```